Calvanto Group Real Estate Company business cards

New business card design, we are generally happy with the basic layout of the existing front of business card, (feel free to change) but require a head shot photo on the back side.

http://www.calvanto.com.au/

Attached logos, and existing business card

------------------------------

Target Market(s)

Real estate

Industry/Entity Type

Real Estate

Contact Information for Business Card

Standard size double sided

Font styles to use
Other font styles liked:
• Futura

Requirements
Must have
• Photo head shot on the back side
Nice to have
• yes
Should not have
• No

```html
<!DOCTYPE html>
<html lang="en">
<head>
<meta charset="utf-8">
<title>Calvanto Group Business Cards</title>
<link href="https://fonts.googleapis.com/css2?family=Jost:wght@300;400;500;600&display=swap" rel="stylesheet">
<style>
  :root {
    --purple: #2f1c5c;
    --purple-deep: #24154a;
    --purple-light: #3e2673;
    --orange: #ee7d13;
    --paper: #f7f7f8;
    --ink: #2b2240;
    --muted: #8a8a93;
    --backdrop: #e3e3e5;
  }
  * { margin: 0; padding: 0; box-sizing: border-box; }
  html, body {
    width: 1200px; height: 1200px; overflow: hidden;
    background: var(--backdrop);
    font-family: "Jost", "Futura", sans-serif;
  }
  .card {
    position: absolute; left: 220px;
    width: 760px; height: 463px;
    border-radius: 24px; overflow: hidden;
    box-shadow: 0 6px 18px rgba(0,0,0,0.18);
  }
  /* Front card */
  .card-front {
    top: 95px;
    background: linear-gradient(160deg, var(--purple-light) 0%, var(--purple) 45%, var(--purple-deep) 100%);
  }
  .headshot {
    position: absolute; left: 422px; top: 18px;
    width: 322px; height: 332px;
    background: linear-gradient(180deg, #eef0f2 0%, #dfe3e8 55%, #2d3a55 100%);
  }
  .tagline {
    position: absolute; left: 58px; top: 165px;
    color: #fff; font-weight: 300; font-size: 38px; line-height: 40px;
  }
  .tagline .accent { color: var(--orange); }
  .brand {
    position: absolute; font-weight: 400; line-height: 1;
  }
  .brand .name { display: block; letter-spacing: -1px; }
  .brand .sub { display: block; text-align: right; letter-spacing: 6px; text-transform: uppercase; }
  .card-front .brand { left: 58px; top: 318px; color: #fff; }
  .card-front .brand .name { font-size: 72px; }
  .card-front .brand .sub { font-size: 12px; margin-top: 2px; }

  /* Back card */
  .card-back {
    top: 640px;
    background: var(--paper);
  }
  .card-back .brand { left: 58px; top: 150px; color: var(--purple); }
  .card-back .brand .name { font-size: 92px; }
  .card-back .brand .sub { font-size: 13px; margin-top: 2px; }
  .band { position: absolute; left: 0; top: 0; }
  .person {
    position: absolute; right: 48px; top: 78px; text-align: right; color: var(--purple);
  }
  .person .full-name { font-size: 28px; font-weight: 600; }
  .person .role { font-size: 15px; color: var(--ink); }
  .divider-top {
    position: absolute; left: 470px; right: 48px; top: 148px;
    border-top: 1px solid #9a9aa3;
  }
  .social {
    position: absolute; right: 48px; top: 170px;
    display: flex; align-items: center; gap: 6px;
    font-size: 16px; color: var(--ink);
  }
  .social .dot { width: 20px; height: 20px; border-radius: 4px; background: var(--orange); }
  .social .label { margin-right: 6px; }
  .abn {
    position: absolute; right: 48px; top: 206px; font-size: 16px; color: var(--ink);
  }
  .divider-contact {
    position: absolute; left: 58px; width: 420px; top: 292px;
    border-top: 1px solid #9a9aa3;
  }
  .contacts {
    position: absolute; left: 90px; top: 304px;
    list-style: none; font-size: 17px; color: var(--ink); line-height: 28px;
  }
  .contacts li { display: flex; align-items: center; gap: 12px; }
  .contacts svg { width: 16px; height: 16px; flex: none; }
</style>
</head>
<body>

<section class="card card-front">
  <p class="tagline">Let us<br>show you<br><span class="accent">property</span></p>
  <div class="brand"><span class="name">calvanto</span><span class="sub">Group</span></div>
  <div class="headshot" role="img" aria-label="Head shot of the director in a suit and tie against a light background"></div>
</section>

<section class="card card-back">
  <svg class="band" width="760" height="463" viewBox="0 0 760 463" aria-hidden="true">
    <polygon points="0,432 505,432 535,402 760,402 760,463 0,463" fill="var(--orange)"/>
    <polygon points="545,342 760,342 760,463 535,463 535,402 545,392" fill="var(--purple)"/>
  </svg>

  <div class="brand"><span class="name">calvanto</span><span class="sub">Group</span></div>

  <div class="person">
    <div class="full-name">Dana Whitfield</div>
    <div class="role">Director</div>
  </div>
  <div class="divider-top"></div>
  <div class="social"><span class="label">Find us:</span><span class="dot"></span><span class="dot"></span><span class="dot"></span></div>
  <div class="abn">ABN: 12 345 678 901</div>

  <div class="divider-contact"></div>
  <ul class="contacts">
    <li>
      <svg viewBox="0 0 16 16"><rect x="3" y="0.5" width="10" height="15" rx="2" fill="var(--orange)"/><rect x="5" y="2.5" width="6" height="9" fill="#fff"/></svg>
      0400 555 218
    </li>
    <li>
      <svg viewBox="0 0 16 16"><circle cx="8" cy="8" r="7" fill="var(--orange)"/><path d="M1 8h14M8 1c-3 3.5-3 10.5 0 14M8 1c3 3.5 3 10.5 0 14" stroke="#fff" stroke-width="1" fill="none"/></svg>
      www.calvanto.com.au
    </li>
    <li>
      <svg viewBox="0 0 16 16"><rect x="0.5" y="3" width="15" height="10" rx="1" fill="var(--orange)"/><path d="M1 3.5l7 5.5 7-5.5" stroke="#fff" stroke-width="1.2" fill="none"/></svg>
      dana.whitfield@calvanto.com.au
    </li>
  </ul>
</section>

</body>
</html>
```